Pet Sitting Business Card

Would like a business card designed for my new pet sitting business
Card needs to match with logo design.
Blue and Orange are the theme colours.

Simple yet sophisticated design

company name:- MEADOWLARK PET CARE
Dana Kovich
Owner
0452716093
dana@meadowlarkpetcare.com.au
www.meadowlarkpetcare.com.au

I'm going to close my deadline early. I will be picking a winner by the 10th of May. Please submit designs before then.
thank you

Target Market(s)

All types of professional pet lovers wishing to have their pet looked after

Industry/Entity Type

Pet

Requirements
Must have
• Logo design
Blue and orange

```html
<!DOCTYPE html>
<html lang="en">
<head>
<meta charset="utf-8">
<title>Meadowlark Pet Care – Business Card</title>
<link href="https://fonts.googleapis.com/css2?family=Exo+2:wght@400;500;700&display=swap" rel="stylesheet">
<style>
  :root {
    --bg: #9a9a9a;
    --paper: #ffffff;
    --orange: #e8892b;
    --blue: #1f8ff0;
    --pill-orange: #c9731f;
    --pill-blue: #1877cf;
    --ink: #2b2b2b;
    --white: #ffffff;
  }
  * { box-sizing: border-box; margin: 0; padding: 0; }
  html, body { width: 1200px; height: 1200px; overflow: hidden; }
  body {
    background: var(--bg);
    font-family: "Exo 2", sans-serif;
    position: relative;
  }
  .card {
    position: absolute;
    top: 215px;
    width: 440px;
    height: 770px;
    background: var(--paper);
    display: flex;
    flex-direction: column;
    box-shadow: 0 8px 24px rgba(0,0,0,0.25);
    overflow: hidden;
  }
  .card--back { left: 120px; }
  .card--front { left: 640px; }

  .card__top {
    display: flex;
    flex-direction: column;
    align-items: center;
    justify-content: center;
    background: var(--paper);
  }
  .card--back .card__top { height: 290px; }
  .card--front .card__top { height: 330px; justify-content: flex-start; padding-top: 95px; }

  .brand {
    display: flex;
    align-items: center;
    justify-content: center;
    gap: 12px;
  }
  .brand__mark {
    width: 16px;
    height: 16px;
    border-radius: 50%;
    background: var(--blue);
  }
  .brand__name {
    font-weight: 700;
    font-size: 26px;
    letter-spacing: 1px;
    color: var(--blue);
    text-align: center;
    line-height: 1.1;
  }

  .person { margin-top: 40px; align-self: flex-start; padding-left: 90px; }
  .person__name {
    font-weight: 500;
    font-size: 24px;
    letter-spacing: 1px;
    color: var(--orange);
    text-transform: uppercase;
  }
  .person__role {
    font-size: 17px;
    letter-spacing: 1px;
    color: var(--ink);
    text-transform: uppercase;
  }

  .band {
    flex: 1;
    display: flex;
    flex-direction: column;
    justify-content: center;
    gap: 16px;
    padding: 0 34px;
  }
  .band--orange { background: var(--orange); }
  .band--blue { background: var(--blue); }
  .card--front .band--orange { flex: 0 0 210px; }
  .card--front .band--blue { flex: 0 0 230px; }

  .pill {
    display: flex;
    align-items: center;
    gap: 14px;
    min-height: 56px;
    padding: 8px 14px;
    border-radius: 8px;
    color: var(--white);
    font-size: 18px;
    letter-spacing: 0.5px;
    line-height: 1.25;
  }
  .band--orange .pill { background: var(--pill-orange); }
  .band--blue .pill { background: var(--pill-blue); }
  .pill__icon {
    flex: 0 0 32px;
    width: 32px;
    height: 32px;
    border: 2px solid var(--white);
    border-radius: 4px;
    display: flex;
    align-items: center;
    justify-content: center;
  }
  .pill__icon svg { width: 18px; height: 18px; fill: var(--white); }
  .pill__icon--plain::after {
    content: "";
    width: 12px;
    height: 12px;
    background: var(--white);
    border-radius: 2px;
  }
  .pill__text { font-size: 16px; }
</style>
</head>
<body>

<section class="card card--back" aria-label="Card back">
  <div class="card__top">
    <div class="brand">
      <span class="brand__mark"></span>
      <div class="brand__name">MEADOWLARK<br>PET CARE</div>
    </div>
  </div>
  <div class="band band--orange">
    <div class="pill"><span class="pill__icon pill__icon--plain"></span><span>pawpage.net/meadowlark</span></div>
  </div>
  <div class="band band--blue">
    <div class="pill"><span class="pill__icon pill__icon--plain"></span><span>chirper.net/meadowlark</span></div>
  </div>
  <div class="band band--orange">
    <div class="pill"><span class="pill__icon pill__icon--plain"></span><span>workline.net/meadowlark</span></div>
  </div>
</section>

<section class="card card--front" aria-label="Card front">
  <div class="card__top">
    <div class="brand">
      <span class="brand__mark"></span>
      <div class="brand__name">MEADOWLARK<br>PET CARE</div>
    </div>
    <div class="person">
      <div class="person__name">Dana Kovich</div>
      <div class="person__role">Owner</div>
    </div>
  </div>
  <div class="band band--orange">
    <div class="pill">
      <span class="pill__icon"><svg viewBox="0 0 24 24"><path d="M6.6 10.8a15 15 0 0 0 6.6 6.6l2.2-2.2a1 1 0 0 1 1-.25 11.4 11.4 0 0 0 3.6.57 1 1 0 0 1 1 1V20a1 1 0 0 1-1 1A17 17 0 0 1 3 4a1 1 0 0 1 1-1h3.5a1 1 0 0 1 1 1c0 1.25.2 2.45.57 3.57a1 1 0 0 1-.25 1z"/></svg></span>
      <span>0452716093</span>
    </div>
    <div class="pill">
      <span class="pill__icon"><svg viewBox="0 0 24 24"><path d="M3 5h18v14H3z M4 6.5v1l8 5 8-5v-1z" fill-rule="evenodd"/></svg></span>
      <span class="pill__text">dana@meadowlarkpetcare.com.au</span>
    </div>
  </div>
  <div class="band band--blue">
    <div class="pill">
      <span class="pill__icon"><svg viewBox="0 0 24 24"><path d="M12 2a10 10 0 1 0 0 20 10 10 0 0 0 0-20zm0 2c.9 1.2 1.6 2.6 2 4h-4c.4-1.4 1.1-2.8 2-4zM4.3 14a8 8 0 0 1 0-4h3.4a16 16 0 0 0 0 4zm1 2h3c.3 1.3.8 2.5 1.5 3.6A8 8 0 0 1 5.3 16zm3-8h-3a8 8 0 0 1 4.5-3.6C9.1 5.5 8.6 6.7 8.3 8zM12 20c-.9-1.2-1.6-2.6-2-4h4c-.4 1.4-1.1 2.8-2 4zm2.3-6H9.7a14 14 0 0 1 0-4h4.6a14 14 0 0 1 0 4zm.9 5.6c.7-1.1 1.2-2.3 1.5-3.6h3a8 8 0 0 1-4.5 3.6zm1.1-5.6a16 16 0 0 0 0-4h3.4a8 8 0 0 1 0 4z"/></svg></span>
      <span class="pill__text">www.meadowlarkpetcare.com.au</span>
    </div>
    <div class="pill">
      <span class="pill__icon"><svg viewBox="0 0 24 24"><path d="M12 2a7 7 0 0 0-7 7c0 5 7 13 7 13s7-8 7-13a7 7 0 0 0-7-7zm0 9.5A2.5 2.5 0 1 1 12 6.5a2.5 2.5 0 0 1 0 5z"/></svg></span>
      <span class="pill__text">24 Wattle Grove Road, Unit 3<br>Street W.</span>
    </div>
  </div>
</section>

</body>
</html>
```